Managed IT services business card design

We haven't needed a business card since the founding of the business in 2005. All our clients have been coming through word of mouth. And lately more and more existing clients are requesting for our business cards to pass on to their contacts in recommending us.
So we needing a business card design. We use various innovative solutions and methodologies to provide IT services to small businesses in managing their IT systems. Our role is the same as an in-house, full-time IT Manager for our clients, but outsourced. So we take care of all our clients' IT needs, just as an IT Manager would be expected to perform.
We have a holding website, which we're happy to leave for now. If we can use the same logo would be great - www.lumadesk.com.au
Preferred colours are shades of are white, grey and black.
We pride our business with the following traits: proactive, good service, prompt response, trustworthy.
Target Market(s)
Small businesses of any industry
Industry/Entity Type
Business

```html
<!DOCTYPE html>
<html lang="en">
<head>
<meta charset="utf-8">
<title>lumadesk business card</title>
<link rel="stylesheet" href="https://fonts.googleapis.com/css2?family=Noto+Sans:wght@400;500&display=swap">
<style>
  :root {
    --backdrop: #e2e2e2;
    --card-white: #ffffff;
    --card-grey: #5a5e63;
    --band-grey: #5d6266;
    --ink: #1c1c1c;
    --ink-soft: #4a4a4a;
    --rule: #2a2a2a;
    --on-grey: #f2f2f2;
  }
  * { margin: 0; padding: 0; box-sizing: border-box; }
  html, body { width: 1200px; height: 680px; overflow: hidden; }
  body {
    background: var(--backdrop);
    font-family: "Noto Sans", sans-serif;
    color: var(--ink);
    position: relative;
  }
  .card {
    position: absolute;
    top: 190px;
    width: 520px;
    height: 300px;
    overflow: hidden;
    box-shadow: 0 2px 6px rgba(0,0,0,0.18);
  }
  /* front */
  .card-front { left: 50px; background: var(--card-white); }
  .rule-top {
    position: absolute; left: 210px; right: 30px; top: 70px;
    height: 1px; background: var(--rule);
  }
  .wordmark {
    position: absolute; left: 28px; top: 92px;
    font-size: 40px; font-weight: 400; letter-spacing: 12px;
    color: var(--ink);
  }
  .rule-bottom {
    position: absolute; left: 28px; width: 250px; top: 156px;
    height: 1px; background: var(--rule);
  }
  .holder { position: absolute; left: 40px; top: 164px; }
  .holder-name { font-size: 17px; font-weight: 400; color: var(--ink); line-height: 1.2; }
  .holder-role { font-size: 12px; color: var(--ink-soft); margin-left: 2px; }
  .contacts {
    position: absolute; left: 40px; top: 196px;
    list-style: none; font-size: 14px; line-height: 18px;
  }
  .contacts li { display: flex; align-items: center; gap: 8px; }
  .contacts svg { width: 13px; height: 13px; fill: var(--ink-soft); }
  .address {
    position: absolute; right: 36px; top: 178px;
    font-size: 13px; line-height: 16px; text-align: right;
  }
  .band {
    position: absolute; left: 0; right: 0; bottom: 0; height: 44px;
    background: var(--band-grey);
    border-top-right-radius: 22px;
    border-top-left-radius: 22px;
    display: flex; align-items: center; justify-content: center;
  }
  .band-url { color: var(--on-grey); font-size: 12px; letter-spacing: 5px; }
  /* back */
  .card-back { left: 630px; background: var(--card-grey); color: var(--on-grey); }
  .back-wordmark {
    position: absolute; left: 0; right: 0; top: 112px; text-align: center;
    font-size: 46px; letter-spacing: 14px; color: var(--on-grey);
  }
  .back-url {
    position: absolute; right: 36px; bottom: 26px;
    font-size: 12px; letter-spacing: 5px; color: var(--on-grey);
  }
</style>
</head>
<body>
  <section class="card card-front" aria-label="Card front">
    <div class="rule-top"></div>
    <div class="wordmark">lumadesk</div>
    <div class="rule-bottom"></div>
    <div class="holder">
      <p class="holder-name">Mark Elwood</p>
      <p class="holder-role">director</p>
    </div>
    <ul class="contacts">
      <li>
        <svg viewBox="0 0 16 16" aria-hidden="true"><path d="M3 1h3l1.5 4-2 1.3a9 9 0 0 0 4.2 4.2L11 8.5l4 1.5v3c0 1-1 2-2 2C7 15 1 9 1 3c0-1 1-2 2-2z"/></svg>
        <span>512 004 2700</span>
      </li>
      <li>
        <svg viewBox="0 0 16 16" aria-hidden="true"><rect x="2" y="6" width="12" height="8" rx="1"/><rect x="4" y="2" width="8" height="5" fill="none" stroke="#4a4a4a" stroke-width="1.4"/></svg>
        <span>512 004 2701</span>
      </li>
      <li>
        <svg viewBox="0 0 16 16" aria-hidden="true"><path d="M1 4h14v9H1z M1 4l7 5 7-5" fill="none" stroke="#4a4a4a" stroke-width="1.5"/></svg>
        <span>info@lumadesk.com</span>
      </li>
    </ul>
    <address class="address" style="font-style:normal">
      4100 Cole Ridge Rd<br>Marden TX 78100
    </address>
    <div class="band"><span class="band-url">www.lumadesk.com</span></div>
  </section>

  <section class="card card-back" aria-label="Card back">
    <div class="back-wordmark">lumadesk</div>
    <div class="back-url">www.lumadesk.com</div>
  </section>
</body>
</html>
```